Morvista Publication Cover

At Morvista (www.morvista.com) we deliver consultancy services based on world-class research and expertise at Australia's national university. We produce many proposals, informal reports and contracts with a simple cover page (see attached example) but occasionally we produce a more formal document that will be delivered to clients in hard copy, displayed on reception tables and generally needs to look more like a professionally produced book than a simple report.

We are looking to develop a front and back cover layer that can be overlaid upon a photographic image. The image will be different to suit each report so the cover should work with a variety of photos. The Morvista website (morvista.com) provides a good indication of our corporate style.
Updates

To all designers, we have decided to guarantee payment on this project. Please reconsider if you declined because the project was initially reimbursable. 

Industry/Entity Type

University

Requirements
Must have
• • Front and back A4 cover design
• Please provide 2 formats - landscape and portrait versions
• Provided in Adobe Illustrator (.ai) format
• Morvista logo and Report Title/Subtitle on the front and editable (see attached)
• Blurb, Disclaimer and Contact Details on back (see attached)
• Corporate fonts attached
• Adhere to overall Morvista style (per the existing template, logo, colour scheme, and style guide (attached) and website)
• It should work with any type of photograph we may want to include (please provide some examples of photos from internet that work well as a demonstration)
• We are open to colour filters, transparency, etc. applied to images to suit template if necessary

```html
<!DOCTYPE html>
<html lang="en">
<head>
<meta charset="utf-8">
<title>Morvista Publication Cover</title>
<link href="https://fonts.googleapis.com/css2?family=Montserrat:wght@400;500;600;700&display=swap" rel="stylesheet">
<style>
  :root {
    --page-bg: #d9d9d9;
    --cover-edge: #c9e3ee;
    --cover-mid: #f3f8fa;
    --brand-blue: #4fa8c9;
    --badge-blue: #5cb6d6;
    --accent-orange: #c98a45;
    --text-grey: #6e6e6e;
    --text-dark: #3f3f3f;
    --photo-light: #e6eaee;
    --photo-mid: #b9c1c9;
    --photo-warm: #e9d8b0;
  }
  * { box-sizing: border-box; margin: 0; padding: 0; }
  html, body { width: 1200px; height: 800px; overflow: hidden; }
  body {
    background: var(--page-bg);
    font-family: "Montserrat", Arial, sans-serif;
    position: relative;
  }
  .cover {
    position: absolute;
    left: 330px; top: 20px;
    width: 540px; height: 760px;
    background: radial-gradient(ellipse 70% 60% at 60% 55%, #ffffff 0%, var(--cover-mid) 45%, var(--cover-edge) 100%);
    box-shadow: 0 6px 18px rgba(0,0,0,0.18);
    overflow: hidden;
  }
  .site-line {
    position: absolute; left: 44px; top: 26px;
    font-size: 9px; color: var(--text-dark);
  }
  .site-line strong { color: var(--accent-orange); font-weight: 600; }
  .cover-photo {
    position: absolute; left: 44px; top: 44px;
    width: 440px; height: 350px;
    background:
      radial-gradient(circle at 48% 42%, var(--photo-warm) 0%, rgba(233,216,176,0) 28%),
      linear-gradient(160deg, var(--photo-light) 0%, var(--photo-mid) 55%, #8d8f93 100%);
    -webkit-mask-image: linear-gradient(200deg, transparent 0%, #000 12%, #000 70%, transparent 100%);
            mask-image: linear-gradient(200deg, transparent 0%, #000 12%, #000 70%, transparent 100%);
  }
  .tagline-badge {
    position: absolute; left: 30px; top: 200px;
    width: 128px; height: 116px;
    background: var(--badge-blue);
    color: #fff;
    display: flex; flex-direction: column; justify-content: center;
    padding: 0 10px;
    text-transform: uppercase; line-height: 1.05;
  }
  .tagline-badge .small { font-size: 13px; font-weight: 500; }
  .tagline-badge .large { font-size: 21px; font-weight: 600; }
  .report-title {
    position: absolute; left: 290px; top: 300px;
    color: var(--brand-blue);
  }
  .report-title h1 { font-size: 40px; font-weight: 600; line-height: 1.0; }
  .report-title h2 { font-size: 28px; font-weight: 600; margin-top: 22px; }
  .submission {
    position: absolute; left: 60px; top: 520px;
    font-size: 15px; line-height: 1.2; color: var(--text-grey);
  }
  .submission .label { color: var(--accent-orange); font-weight: 600; }
  .submission .role { color: var(--text-dark); font-weight: 600; }
  .brand {
    position: absolute; left: 60px; top: 670px;
    display: flex; align-items: center; gap: 12px;
  }
  .brand-name { font-size: 44px; font-weight: 500; color: var(--text-grey); letter-spacing: -0.5px; }
  .brand-dot { width: 30px; height: 30px; border-radius: 50%; background: var(--brand-blue); }
  .contact-box {
    position: absolute; left: 360px; top: 540px;
    font-size: 9px; color: var(--text-dark); line-height: 1.6;
  }
  .contact-box h3 { font-size: 11px; font-weight: 700; margin-bottom: 2px; }
  .contact-box dl { display: grid; grid-template-columns: 40px auto; }
  .contact-box dt { color: var(--text-grey); }
</style>
</head>
<body>
  <main class="cover">
    <p class="site-line">Visit our site at <strong>www.morvista.com</strong></p>
    <div class="cover-photo" role="img" aria-label="Photograph of business people in a boardroom presenting to a large grid of screens showing a glowing globe"></div>
    <div class="tagline-badge">
      <span class="small">World Class</span>
      <span class="large">Expertise</span>
      <span class="large">Applied</span>
      <span class="small">Globally</span>
    </div>
    <div class="report-title">
      <h1>Main<br>Heading</h1>
      <h2>Subheading</h2>
    </div>
    <div class="submission">
      <p class="label">Submitted</p>
      <p>Insert Date</p>
      <p class="label">Contact</p>
      <p class="role">Manager</p>
      <p>Insert Title</p>
      <p>T: +61 2 5550 XXXX | F: + 61 2 5550 5875</p>
      <p>Insert Email</p>
    </div>
    <div class="brand">
      <span class="brand-name">Morvista</span>
      <span class="brand-dot"></span>
    </div>
    <div class="contact-box">
      <h3>Get in touch</h3>
      <dl>
        <dt>phone:</dt><dd>+61 2 5550 6101</dd>
        <dt>e-mail:</dt><dd>ContactUs@morvista.com</dd>
      </dl>
    </div>
  </main>
</body>
</html>
```